Business Card Design

Business Card for professional consulting firm working with large financial institutions.

Target Market(s)

Executive buyers

Industry/Entity Type

Banking

Contact Information for Business Card

Mild creativity wanted. Not boring, but do elaborate artwork.

Font styles to use
Serif
Sans Serif

Colors

Designer to choose colors to be used in the design.

Requirements
Must have
• Standard business card features - company name, individual name, telephone, website, email, locations.
Nice to have
• Two colors
Should not have
• too many colors, fancy printing, cartoons.

```html
<!DOCTYPE html>
<html lang="en">
<head>
<meta charset="utf-8">
<title>Northvale Advisory – Business Card</title>
<link href="https://fonts.googleapis.com/css2?family=Lato:wght@400;700&display=swap" rel="stylesheet">
<style>
  :root {
    --backdrop: #999999;
    --card-dark: #111111;
    --card-blue: #002f87;
    --ink-light: #ffffff;
    --rule: #d9d9d9;
  }
  * { margin: 0; padding: 0; box-sizing: border-box; }
  html, body {
    width: 1200px; height: 900px; overflow: hidden;
    background: var(--backdrop);
    font-family: "Lato", Arial, sans-serif;
    color: var(--ink-light);
  }
  .card {
    position: absolute;
    width: 478px; height: 294px;
  }
  .card--front {
    left: 120px; top: 275px;
    background: var(--card-dark);
    border-radius: 0 46px 0 46px;
  }
  .card--back {
    left: 606px; top: 274px;
    background: var(--card-blue);
    border-radius: 46px 0 46px 0;
  }
  .brand {
    position: absolute;
    font-weight: 400;
    color: var(--ink-light);
    white-space: nowrap;
    display: flex; align-items: center;
  }
  .brand__dot {
    display: inline-block; border-radius: 50%;
    background: var(--ink-light);
  }
  .card--front .brand {
    right: 38px; top: 95px; font-size: 21px; gap: 8px;
  }
  .card--front .brand__dot { width: 9px; height: 9px; }
  .card--back .brand {
    left: 0; right: 0; top: 128px; justify-content: center;
    font-size: 30px; gap: 12px;
  }
  .card--back .brand__dot { width: 12px; height: 12px; }

  .person { position: absolute; left: 28px; top: 168px; right: 28px; }
  .person__name {
    font-size: 17px; font-weight: 700; letter-spacing: 0.3px;
    text-transform: uppercase; line-height: 20px;
  }
  .person__role-row { display: flex; align-items: center; gap: 10px; }
  .person__role { font-size: 13px; line-height: 16px; white-space: nowrap; }
  .person__rule { flex: 1; height: 1px; background: var(--rule); }

  .address {
    position: absolute; left: 28px; top: 233px;
    font-size: 13px; line-height: 18px; font-style: normal;
  }
  .contact {
    position: absolute; right: 30px; top: 215px;
    list-style: none; font-size: 13px; line-height: 18px;
    text-align: right;
  }
  .contact__item { display: flex; align-items: center; justify-content: flex-end; gap: 5px; }
  .contact__icon { width: 11px; height: 11px; fill: var(--ink-light); }
</style>
</head>
<body>
  <section class="card card--front" aria-label="Card front">
    <div class="brand"><span class="brand__name">Northvale Advisory</span><span class="brand__dot"></span></div>

    <div class="person">
      <p class="person__name">Jonathan Smith</p>
      <div class="person__role-row">
        <span class="person__role">Managing Director</span>
        <span class="person__rule"></span>
      </div>
    </div>

    <address class="address">12345, Address Goes Here<br>Country Name, 123456.</address>

    <ul class="contact">
      <li class="contact__item">044-123 456 789
        <svg class="contact__icon" viewBox="0 0 12 12" aria-hidden="true"><path d="M1 4 Q6 0 11 4 L9.5 5.5 L8 4.3 L8 3.5 Q6 3 4 3.5 L4 4.3 L2.5 5.5 Z M3 6 L9 6 L10 10.5 L2 10.5 Z"/></svg>
      </li>
      <li class="contact__item">info@webname.com
        <svg class="contact__icon" viewBox="0 0 12 12" aria-hidden="true"><path d="M1 2.5 H11 V9.5 H1 Z M1.8 3.2 L6 6.3 L10.2 3.2" stroke="#111" stroke-width="0.8" fill="#fff"/></svg>
      </li>
      <li class="contact__item">www.websitename.com
        <svg class="contact__icon" viewBox="0 0 12 12" aria-hidden="true"><circle cx="6" cy="6" r="5"/><path d="M3.5 4 Q5 3 5.5 5 Q4 6.5 5.5 8.5 M7 2.5 Q8.5 4 8 6" stroke="#111" stroke-width="0.9" fill="none"/></svg>
      </li>
    </ul>
  </section>

  <section class="card card--back" aria-label="Card back">
    <div class="brand"><span class="brand__name">Northvale Advisory</span><span class="brand__dot"></span></div>
  </section>
</body>
</html>
```